Post Card Design - Photo on front, details on back. Logo on both sides.

Back: See the photo of my old card. The back worked well, as it gave me lots of space to write on. The address details are still correct, but the logo has changed to Josephine Sans. Logo can be on one line or on two (if two, align it on the left).
Don't include the 'BEAUTIFUL WEDDING DRESSES...' bit.
I'd like to print this on thicker, slightly coarse paper, so don't go too small on detail.
Here are the Trelo paper details: Paper Stock: Natural Uncoated
Paper Thickness: Premium
Finish: None
Front of Card: I'd like to see options for both pictures:
I think the painted image would look best with a frame in a pale shade and the logo in the frame fairly subtle.
The actual dress photo I'd like to see cropped a bit like in my mock up. You'll need to have a look at how the logo would be best placed on this. You can place it anywhere, or add a banner.
See my website for my brand's look: mirelhoffkin.co.nz
Target Market(s)
Brides
Industry/Entity Type
Wedding Dresses
Contact Information for Business Card
Front: Photo and logo. Back: with details and lots of empty space. See attached photos for loose brief.
Other font styles liked:
- Josephine Sans
Requirements
Must have
- I hand-write the gown designs and price on the back of the card, so there needs to be plenty of empty space.
Nice to have
- As per brief.
Should not have
- It must look clean, romantic, modern. Timeless.

```html
<!DOCTYPE html>
<html lang="en">
<head>
<meta charset="utf-8">
<title>Mirel Hoffkin — Postcard Back</title>
<link rel="stylesheet" href="https://fonts.googleapis.com/css2?family=Josefin+Sans:wght@300&family=Source+Sans+3:wght@300&display=swap">
<style>
  :root {
    --paper: #ffffff;
    --ink: #111111;
    --band: #d3d3d5;
    --band-text: #2e2e30;
    --icon: #f4f4f5;
  }
  html, body {
    margin: 0;
    padding: 0;
    overflow: hidden;
    background: var(--paper);
  }
  .postcard-back {
    position: relative;
    width: 1200px;
    height: 800px;
    background: var(--paper);
    overflow: hidden;
  }
  .wordmark {
    position: absolute;
    left: 120px;
    top: 52px;
    margin: 0;
    font-family: "Josefin Sans", sans-serif;
    font-weight: 300;
    font-size: 55px;
    letter-spacing: 2.5px;
    line-height: 1;
    color: var(--ink);
  }
  .writing-space {
    position: absolute;
    left: 0;
    top: 140px;
    width: 1200px;
    height: 580px;
  }
  .contact-band {
    position: absolute;
    left: 0;
    bottom: 0;
    width: 1200px;
    height: 78px;
    background: var(--band);
  }
  .contact-item {
    position: absolute;
    top: 0;
    height: 78px;
    display: flex;
    align-items: center;
    gap: 6px;
    font-family: "Source Sans 3", sans-serif;
    font-weight: 300;
    font-size: 30px;
    color: var(--band-text);
    white-space: nowrap;
  }
  .contact-item svg {
    flex: none;
    fill: none;
    stroke: var(--icon);
    stroke-width: 1.6;
  }
  .contact-phone { left: 118px; }
  .contact-web { left: 380px; }
  .contact-email { left: 711px; gap: 12px; }
</style>
</head>
<body>
  <main class="postcard-back">
    <h1 class="wordmark">MIREL HOFFKIN</h1>
    <div class="writing-space"></div>
    <footer class="contact-band">
      <div class="contact-item contact-phone">
        <svg width="16" height="22" viewBox="0 0 16 22" aria-hidden="true">
          <path d="M5 2 L2 3 C0 8 3 16 9 20 L12 19 L11 14 L8 14 C6 11 5 8 6 6 L8 5 Z" fill="var(--icon)" stroke="none"/>
        </svg>
        <span>0204 555 0187</span>
      </div>
      <div class="contact-item contact-web">
        <svg width="22" height="22" viewBox="0 0 22 22" aria-hidden="true">
          <circle cx="11" cy="11" r="9.5"/>
          <ellipse cx="11" cy="11" rx="4.2" ry="9.5"/>
          <line x1="1.5" y1="11" x2="20.5" y2="11"/>
          <line x1="3" y1="6" x2="19" y2="6"/>
          <line x1="3" y1="16" x2="19" y2="16"/>
        </svg>
        <span>mirelhoffkin.co.nz</span>
      </div>
      <div class="contact-item contact-email">
        <svg width="20" height="16" viewBox="0 0 20 16" aria-hidden="true">
          <rect x="1" y="2" width="18" height="12"/>
          <path d="M1 2 L10 9 L19 2 M1 14 L8 8 M19 14 L12 8"/>
        </svg>
        <span>mirel@mirelhoffkin.co.nz</span>
      </div>
    </footer>
  </main>
</body>
</html>
```